Create an awesome website for a medical clinic

This is a new website for a doctor's office. The site should be clean and modern, easy to navigate.

This is a wellness clinic, we want to help our clients have a healthy, active lifestyle. It should be friendly and inviting, and easy for them to call or schedule an appointment.

The site should be responsive and designed using the attached Bootstrap 3 PSD.

We will provide stock photos, until then please use stock photos from:

pixelharbor.com or
framequarry.com (preferred)

Some example sites of clean and modern designs that we like:

https://tulsaspinecare.com/
http://reachpastjoints.com/
http://turninghealthier.com/

Also attached is a temporary logo you can use.

Reason: Thank you everyone for your great designs - we need a little more time so I'm extending the project.

Need extra days to review

Also, the colors in the new logo I just linked to are the final colors of the logo, so feel free to use any complimentary colors to it.

Hi everyone, The boss wants to change the layout of the site a little bit - here's the revised layout: https://www.filecrate.com/s/k9rt31vx2qp84zn/notes%2011_29_2017.pdf?dl=0 And the graphic assets you can use are here: https://www.filecrate.com/s/k9rt31vx2qp84zn/notes%2011_29_2017.pdf?dl=0 Feel free to change the background color of the "topbar", and change the icons of the "why people trust us" if you want, these are just temporary placeholders. Thanks for your patience and hard work!

Target Market(s)

People seeking medical treatment (wellness clinic)

Industry/Entity Type

Doctor

Number of Pages Required

1 page

Font styles to use
Sans Serif

Colors
0592cd
33a6d7
abd037
9bcb3c

Requirements
Must have
• The home page should have: a strong hero image/slideshow, clinic phone number should be prominent and at the top of the page (in the nav), a "what to expect" section (this is like a FAQs section - see attachment), and a strong call to action (a button to call or schedule an appointment).
• The what to expect section is useful so that prospective clients can determine if we're a good fit for them or not. It's a basic, first-step pre-qualification block of information.
• Social media icons which links to our social media profiles should be included.
Nice to have
• - Link to 3 most recent blog entries
• - Testimonials
• - How a multilevel nav menu looks.

```html
<!DOCTYPE html>
<html lang="en">
<head>
<meta charset="utf-8">
<title>Fernway Medical Clinic</title>
<link href="https://fonts.googleapis.com/css2?family=Montserrat:wght@400;500;600;700&family=Open+Sans:ital,wght@0,400;0,600;1,400&display=swap" rel="stylesheet">
<style>
:root{
  --green:#13932f;
  --green-dark:#0f7f27;
  --blue:#3c7dc2;
  --blue-light:#5a93cf;
  --blue-dark:#1f5a9a;
  --ink:#2b2b2b;
  --body:#555;
  --grey-bg:#f0f0f0;
  --tab-bg:#e4e4e4;
  --dark:#1f1f1f;
}
*{box-sizing:border-box;margin:0;padding:0}
html,body{width:1200px;height:3051px;overflow:hidden}
body{font-family:"Open Sans",Arial,sans-serif;color:var(--body);background:#fff;position:relative}
.abs{position:absolute}
h2.section-title{font-family:"Montserrat",Arial,sans-serif;font-weight:600;font-size:31px;color:var(--blue);letter-spacing:.5px}
h2.section-title::after{content:"";display:block;width:56px;height:3px;background:var(--green);margin-top:10px}
.para{font-size:13.5px;line-height:21px;color:var(--body)}
.btn{display:flex;align-items:center;justify-content:center;background:var(--green);color:#fff;font-family:"Montserrat",Arial,sans-serif;font-size:15px;font-weight:500;border-radius:3px;text-transform:uppercase}
.photo{border-radius:2px}

/* header */
.header{top:0;left:0;width:1200px;height:106px;background:#fff}
.brand{left:112px;top:34px;font-family:"Montserrat",sans-serif;font-weight:700;font-size:30px;line-height:36px;color:var(--green)}
.callnow{right:110px;top:36px;font-family:"Montserrat",sans-serif;font-size:29px;color:var(--green)}
.callnow b{color:var(--blue);font-weight:600}
.navbar{top:106px;left:0;width:1200px;height:40px;background:var(--blue)}
.nav{left:112px;top:0;height:40px;display:flex;gap:41px;align-items:center;list-style:none}
.nav li{font-family:"Montserrat",sans-serif;font-size:13.5px;color:#fff;text-transform:uppercase}
.nav li.active{border-bottom:2px solid #fff;padding-bottom:2px}
.nav-cta{left:841px;top:0;width:247px;height:40px;background:var(--green);color:#fff;font-family:"Montserrat",sans-serif;font-size:13.5px;display:flex;align-items:center;justify-content:center}

/* hero */
.hero{top:146px;left:0;width:1200px;height:442px;background:linear-gradient(100deg,#5d6166 0%,#8a8d91 35%,#74777b 65%,#55585c 100%)}
.hero h1{top:150px;left:0;width:1200px;text-align:center;font-family:"Montserrat",sans-serif;font-weight:700;font-size:53px;color:#fff;letter-spacing:3px}
.hero p{top:216px;left:0;width:1200px;text-align:center;font-family:"Montserrat",sans-serif;font-size:16px;color:#fff;letter-spacing:1.2px}
.hero .btn{left:496px;top:260px;width:208px;height:40px}
.arrow{top:206px}

/* about */
.about{top:588px;left:0;width:1200px;height:313px}
.hours{left:698px;top:59px;width:390px;height:193px;background:#fff;box-shadow:0 3px 8px rgba(0,0,0,.25);border-radius:4px;overflow:hidden}
.hours header{height:47px;background:var(--blue);color:#fff;font-family:"Montserrat",sans-serif;font-size:22px;letter-spacing:1.5px;text-align:center;line-height:47px}
.hours .row{display:flex;justify-content:space-between;padding:0 14px;height:48px;align-items:center;font-size:15px;color:#333;border-bottom:1px solid #e6e6e6}
.hours .row:last-child{border:0;height:50px}
.hours .row.sun span:first-child{color:var(--blue)}

/* what we do */
.services{top:901px;left:0;width:1200px;height:452px;background:var(--grey-bg)}
.tabs{left:112px;top:197px;width:307px;list-style:none}
.tabs li{height:40px;line-height:40px;padding-left:24px;background:var(--tab-bg);color:#333;font-family:"Montserrat",sans-serif;font-size:15px;text-transform:uppercase;position:relative}
.tabs li.active{background:var(--blue);color:#fff}
.tabs li.active::after{content:"";position:absolute;right:-20px;top:0;border-left:20px solid var(--blue);border-top:20px solid transparent;border-bottom:20px solid transparent}
.service-title{left:488px;top:56px;font-family:"Montserrat",sans-serif;font-size:21px;color:var(--green)}
/* expect */
.expect{top:1353px;left:0;width:1200px;height:472px}
.expect-photo{left:0;top:0;width:600px;height:472px;background:linear-gradient(90deg,#9a8a74,#c9bfb1 50%,#7e7165)}
.expect-panel{left:600px;top:0;width:600px;height:472px;background:var(--blue)}
.expect-panel h2{position:absolute;left:26px;top:50px;font-family:"Montserrat",sans-serif;font-weight:600;font-size:31px;color:#fff}
.expect-panel h2::after{content:"";display:block;width:56px;height:2px;background:#fff;margin-top:10px;opacity:.8}
.acc{left:26px;width:462px;height:35px;background:var(--blue-light);color:#fff;font-family:"Montserrat",sans-serif;font-size:15px;display:flex;justify-content:space-between;align-items:center;padding:0 22px 0 22px;border-radius:2px}
.acc b{font-size:20px;font-weight:600}
.acc-body{left:34px;top:225px;width:446px;font-size:13.5px;line-height:20px;color:#c9dcf2}

/* testimonial */
.testi{top:1825px;left:0;width:1200px;height:296px}
.quote-photo{left:447px;top:63px;width:171px;height:171px;background:radial-gradient(circle at 50% 45%,#c89a7e,#6e4a36 80%);box-shadow:0 2px 6px rgba(0,0,0,.3);border:4px solid #fff}
/* blog */
.blog{top:2121px;left:0;width:1200px;height:590px;background:var(--grey-bg)}
.card{background:#fff;border-radius:3px;box-shadow:0 1px 3px rgba(0,0,0,.1);overflow:hidden}
.card h3{font-family:"Montserrat",sans-serif;font-weight:500;font-size:21px;color:#222}
.meta{font-size:12.5px;font-style:italic;color:#777;margin:10px 0 8px;display:flex;align-items:center;gap:6px}
.card .para{font-size:13px;line-height:21px}
.more{font-family:"Montserrat",sans-serif;font-weight:600;color:var(--green);font-size:15px;margin-top:10px}
/* footer */
.footer{top:2711px;left:0;width:1200px;height:301px}
.foot-left{left:0;top:0;width:529px;height:301px;background:var(--green)}
.foot-right{left:529px;top:0;width:671px;height:301px;background:var(--blue)}
.foot-h{font-family:"Montserrat",sans-serif;font-size:21px;color:#9cd3a9}
.foot-right .foot-h{color:#fff;font-weight:600}
.contact-list{list-style:none;margin-top:20px}
.contact-list li{display:flex;gap:12px;font-size:12.5px;line-height:18px;color:#cde8d3;margin-bottom:12px}
.links{list-style:none;margin-top:20px}
.links li{font-size:12.5px;color:#cde8d3;margin-bottom:8px}
.field{height:33px;background:var(--blue-light);border-radius:3px;color:#d5e4f5;font-size:13px;padding-left:22px;line-height:33px;width:254px}
.submit{background:var(--blue-dark);color:#fff;font-family:"Montserrat",sans-serif;font-weight:600;letter-spacing:1.5px;font-size:16px;text-align:center;padding:0}
.bottom{top:3012px;left:0;width:1200px;height:39px;background:var(--dark);color:#ccc;font-size:12.5px}
</style>
</head>
<body>

<header class="abs header">
  <div class="abs brand">Fernway Medical Clinic</div>
  <div class="abs callnow">CALL US NOW: <b>5550 218 447</b></div>
</header>
<nav class="abs navbar">
  <ul class="abs nav">
    <li class="active">Home</li><li>About us</li><li>What to expect</li><li>Testimonial</li><li>Blog</li><li>Contact us</li>
  </ul>
  <div class="abs nav-cta">SCHEDULE AN APPOINTMENT</div>
</nav>

<section class="abs hero" role="img" aria-label="Photo of a doctor's hands writing notes at a clinic desk">
  <svg class="abs arrow" style="left:32px" width="36" height="24" viewBox="0 0 36 24"><path d="M34 12H3M13 2L3 12l10 10" stroke="#ddd" stroke-width="2" fill="none"/></svg>
  <svg class="abs arrow" style="right:32px" width="36" height="24" viewBox="0 0 36 24"><path d="M2 12h31M23 2l10 10-10 10" stroke="#ddd" stroke-width="2" fill="none"/></svg>
  <h1 class="abs">WELLNESS CLINIC</h1>
  <p class="abs">WE WANT TO HELP OUR CLIENTS HAVE A HEALTHY, ACTIVE LIFESTYLE</p>
  <div class="abs btn">Read more</div>
</section>

<section class="abs about">
  <h2 class="abs section-title" style="left:112px;top:52px">ABOUT US</h2>
  <p class="abs para" style="left:112px;top:116px;width:548px">Lorem Ipsum is simply dummy text of the printing and typesetting industry. Lorem Ipsum has been the industry's standard dummy text ever since the 1500s, when an unknown printer took a galley of type and scrambled it to make a type specimen book. It has survived not only five centuries.</p>
  <div class="abs btn" style="left:112px;top:215px;width:140px;height:37px">Read more</div>
  <div class="abs hours">
    <header>OPENING HOURS</header>
    <div class="row"><span>Monday - Friday</span><span>08 Am : 17 Pm</span></div>
    <div class="row"><span>Saturday</span><span>08 Am : 17 Pm</span></div>
    <div class="row sun"><span>Sunday</span><span>08 Am : 10 Am</span></div>
  </div>
</section>

<section class="abs services">
  <h2 class="abs section-title" style="left:112px;top:55px">WHAT WE DO</h2>
  <p class="abs para" style="left:112px;top:115px;width:335px">Lorem Ipsum is simply dummy text of the printing and typesetting industry. Lorem Ipsum has been the industry's standard dummy.</p>
  <ul class="abs tabs">
    <li>Neurological Chiropractic</li>
    <li class="active">Eye Care and Surgery</li>
    <li>Diabetes Treatment</li>
    <li>About Kids and Pregnancy</li>
    <li>Emergency Services</li>
  </ul>
  <div class="abs service-title">Eye Care Surgery</div>
  <p class="abs para" style="left:488px;top:92px;width:600px">It is a long established fact that a reader will be distracted by the readable content of a page when looking at its layout. The point of using Lorem Ipsum is that it has a more-or-less normal distribution of letters, as opposed to using 'Content here.</p>
  <div class="abs photo" role="img" aria-label="Patient lying under an eye examination microscope" style="left:490px;top:173px;width:285px;height:199px;background:linear-gradient(135deg,#e8eef2,#b9c7d0 60%,#7fa9c4)"></div>
  <div class="abs photo" role="img" aria-label="Surgeons operating with a surgical microscope" style="left:803px;top:173px;width:285px;height:199px;background:linear-gradient(135deg,#3f6e8f,#2b5b86 50%,#4d86b5)"></div>
</section>

<section class="abs expect">
  <div class="abs expect-photo" role="img" aria-label="Receptionist helping an older patient at the clinic front desk"></div>
  <div class="abs expect-panel">
    <h2>WHAT TO EXPECT</h2>
    <div class="abs acc" style="top:122px"><span>Lorem Ipsum is simply dummy text.</span><b>+</b></div>
    <div class="abs acc" style="top:177px"><span>Lorem Ipsum is simply dummy text.</span><b>-</b></div>
    <p class="abs acc-body">It is a long established fact that a reader will be distracted by the readable content of a page when looking at its layout. The point of using Lorem Ipsum is that it has a more-or-less normal distribution of letters, as opposed to using 'Content here.</p>
    <div class="abs acc" style="top:321px"><span>Lorem Ipsum is simply dummy text.</span><b>+</b></div>
    <div class="abs acc" style="top:376px"><span>Lorem Ipsum is simply dummy text.</span><b>+</b></div>
  </div>
</section>

<section class="abs testi">
  <h2 class="abs section-title" style="left:112px;top:50px">TESTIMONIAL</h2>
  <p class="abs para" style="left:112px;top:115px;width:310px">Contrary to popular belief, Lorem Ipsum is not simply random text. It has roots in a piece of classical Latin literature from 45 BC.</p>
  <div class="abs btn" style="left:112px;top:197px;width:173px;height:37px">More reviews</div>
  <div class="abs quote-photo" role="img" aria-label="Portrait of the reviewing client"></div>
  <svg class="abs" style="left:632px;top:50px" width="58" height="44" viewBox="0 0 58 44"><path d="M4 44V24C4 10 12 3 24 1v8c-7 2-10 7-10 13h10v22zM34 44V24C34 10 42 3 54 1v8c-7 2-10 7-10 13h10v22z" fill="#f2f2f2"/></svg>
  <div class="abs" style="left:645px;top:82px;font-family:'Montserrat',sans-serif;font-size:16px;color:#222">The standard chunk of Lorem Ipsum used</div>
  <p class="abs para" style="left:645px;top:109px;width:420px;font-size:13px">All the Lorem Ipsum generators on the Internet tend to repeat predefined chunks as necessary, making this the first true generator on the Internet.</p>
  <div class="abs" style="left:645px;top:174px;font-style:italic;font-weight:600;font-size:15px;color:#222">Jenny Doe</div>
  <div class="abs" style="left:645px;top:196px;font-size:12px;color:#888">- Sales Manager</div>
  <svg class="abs" style="left:1052px;top:193px" width="40" height="16" viewBox="0 0 40 16"><path d="M8 2L2 8l6 6M32 2l6 6-6 6" stroke="#444" stroke-width="2" fill="none"/></svg>
</section>

<section class="abs blog">
  <h2 class="abs section-title" style="left:112px;top:52px">RECENT BLOG</h2>

  <article class="abs card" style="left:112px;top:127px;width:641px;height:189px">
    <div class="abs" role="img" aria-label="Patient at an eye examination machine" style="left:0;top:0;width:319px;height:189px;background:linear-gradient(120deg,#2f6c99,#9bb7c9 55%,#d8dde0)"></div>
    <div class="abs" style="left:345px;top:20px;width:280px">
      <h3>Lorem ipsum is simple</h3>
      <div class="meta"><svg width="12" height="12" viewBox="0 0 12 12"><rect x="1" y="2" width="10" height="9" fill="none" stroke="#3c7dc2"/><path d="M1 5h10" stroke="#3c7dc2"/></svg>17th September, 2017</div>
      <p class="para">Contrary to popular belief, Lorem Ipsum is not simply random text. It has roots in a piece of classical Latin...</p>
      <div class="more">Read More &rsaquo;</div>
    </div>
  </article>

  <article class="abs card" style="left:112px;top:342px;width:641px;height:189px">
    <div class="abs" role="img" aria-label="Child at a dental check-up" style="left:0;top:0;width:319px;height:189px;background:linear-gradient(120deg,#8a5a45,#c9977a 50%,#3f9aa8)"></div>
    <div class="abs" style="left:345px;top:20px;width:280px">
      <h3>Lorem ipsum is simple</h3>
      <div class="meta"><svg width="12" height="12" viewBox="0 0 12 12"><rect x="1" y="2" width="10" height="9" fill="none" stroke="#3c7dc2"/><path d="M1 5h10" stroke="#3c7dc2"/></svg>17th September, 2017</div>
      <p class="para">Contrary to popular belief, Lorem Ipsum is not simply random text. It has roots in a piece of classical Latin...</p>
      <div class="more">Read More &rsaquo;</div>
    </div>
  </article>

  <article class="abs card" style="left:781px;top:127px;width:307px;height:404px">
    <div class="abs" role="img" aria-label="Doctor consulting with a patient in an office" style="left:0;top:0;width:307px;height:201px;background:linear-gradient(135deg,#6e5a48,#d9d2c8 55%,#4a3b31)"></div>
    <div class="abs" style="left:24px;top:219px;width:264px">
      <h3>Lorem ipsum is simple</h3>
      <div class="meta"><svg width="12" height="12" viewBox="0 0 12 12"><rect x="1" y="2" width="10" height="9" fill="none" stroke="#3c7dc2"/><path d="M1 5h10" stroke="#3c7dc2"/></svg>17th September, 2017</div>
      <p class="para">Contrary to popular belief, Lorem Ipsum is not simply random text. It has roots in a piece of classical Latin...</p>
      <div class="more">Read More &rsaquo;</div>
    </div>
  </article>
</section>

<footer class="abs footer">
  <div class="abs foot-left">
    <div class="abs" style="left:112px;top:58px;width:220px">
      <div class="foot-h">Contact Info</div>
      <ul class="contact-list">
        <li><svg width="10" height="14" viewBox="0 0 10 14"><path d="M5 0a5 5 0 00-5 5c0 4 5 9 5 9s5-5 5-9a5 5 0 00-5-5zm0 7a2 2 0 110-4 2 2 0 010 4z" fill="#fff"/></svg><span>240 Cedar Ave, Suite 300<br>Lakeview, OR 97630</span></li>
        <li><svg width="12" height="12" viewBox="0 0 12 12"><path d="M3 0l2 3-1.5 1.5a7 7 0 004 4L9 7l3 2-1.5 3C5 12 0 7 0 1.5z" fill="#fff"/></svg><span>(555) 214-3390</span></li>
        <li><svg width="13" height="10" viewBox="0 0 13 10"><rect width="13" height="10" fill="#fff"/><path d="M0 0l6.5 5L13 0" stroke="#13932f" fill="none"/></svg><span>contact@fernwaymedical.com</span></li>
      </ul>
      <div style="display:flex;gap:14px;margin-top:4px">
        <svg width="10" height="10"><rect width="10" height="10" fill="#9cd3a9"/></svg>
        <svg width="10" height="10"><rect width="10" height="10" fill="#9cd3a9"/></svg>
        <svg width="10" height="10"><rect width="10" height="10" fill="#9cd3a9"/></svg>
      </div>
    </div>
    <div class="abs" style="left:362px;top:58px">
      <div class="foot-h">Quick Link</div>
      <ul class="links"><li>Home</li><li>About us</li><li>What to expect</li><li>Blog</li><li>Contact us</li></ul>
    </div>
  </div>
  <div class="abs foot-right">
    <div class="abs foot-h" style="left:26px;top:58px">Schedule An Appointment</div>
    <div class="abs field" style="left:26px;top:102px">Name</div>
    <div class="abs field" style="left:305px;top:102px">Email</div>
    <div class="abs field" style="left:26px;top:155px">Phone</div>
    <div class="abs field" style="left:305px;top:155px">Proposed Date</div>
    <div class="abs field" style="left:26px;top:208px">Proposed Time</div>
    <div class="abs field submit" style="left:305px;top:208px">SUBMIT</div>
  </div>
</footer>

<div class="abs bottom">
  <span class="abs" style="left:112px;top:11px">Fernway Medical Clinic© 2017 &nbsp;|&nbsp; All Rights Reserved.</span>
  <svg class="abs" style="left:1072px;top:12px" width="16" height="16" viewBox="0 0 16 16"><path d="M8 1L1 9h4v6h6V9h4z" fill="#fff"/></svg>
</div>

</body>
</html>
```